My Music Collection - vinyl, CD

1. I want to catalogue my vinyl record collection, because it's hard to remember all the albums (and singles) I own, and that's a problem because I sometimes double up.

2. I'd like to identify my music by a) artist b) album title c) song title

3. I'd like the option of recording the quality of the album just in case I happen to find one that is a better quality

4. I would also like the album cover image, genre, record label, track listing and production date to automatically download

Target Market(s)

There has been a huge resurgence in the vinyl record market lately, but lots of people also have a CD collection. I want this app for the over 45s who have better things to remember than which albums they have!

Requirements
Must have
• 1. Be able to list my music by a) artist b) song title

2. Ideally, i would like to work with the designer when its time to update the app in the future.

3. Be creative, if I've left something out - put it in! Have a go!
Nice to have
• 1. link to something like Melvox - so i can identify songs

2. I would also like to list my singles

I would ideally like to use this app on my Vexa, and of course my Kolbet - but, i dont want the Vexa app to look like a cropped version of the Kolbet app (is that possible)?

```html
<!DOCTYPE html>
<html lang="en">
<head>
<meta charset="utf-8">
<title>Spindle – Album Detail</title>
<link href="https://fonts.googleapis.com/css2?family=Arimo:wght@400;700&display=swap" rel="stylesheet">
<style>
  :root {
    --header-top: #3a3c40;
    --header-bottom: #222427;
    --search-fill: #45474b;
    --search-edge: #1a1b1d;
    --hero-top: #8a6aa3;
    --hero-bottom: #8d7fae;
    --body-top: #8b8db8;
    --body-bottom: #8a80ae;
    --text-light: #ffffff;
    --text-soft: #e9e6f2;
    --green-top: #4caf33;
    --green-bottom: #2f9320;
    --red-top: #f8535d;
    --red-bottom: #ee3a45;
    --blue-top: #2a86d6;
    --blue-bottom: #1b60b6;
    --tab-top: #3a3b3e;
    --tab-bottom: #27282b;
    --tab-icon: #8d8e92;
    --tab-label: #a9aaae;
    --cover-paper: #e8dcbf;
    --cover-accent: #6fb3b0;
  }
  * { box-sizing: border-box; margin: 0; padding: 0; }
  html, body { width: 800px; height: 1200px; overflow: hidden; }
  body {
    font-family: "Arimo", Arial, sans-serif;
    background: linear-gradient(var(--body-top), var(--body-bottom));
    position: relative;
    color: var(--text-light);
  }
  .app-header {
    position: absolute; left: 0; top: 0; width: 800px; height: 115px;
    background: linear-gradient(var(--header-top), var(--header-bottom));
    border-bottom: 2px solid #18191b;
  }
  .app-name {
    position: absolute; left: 26px; top: 26px;
    font-size: 46px; font-weight: 700; color: var(--text-light);
    letter-spacing: 0.5px;
  }
  .search-field {
    position: absolute; left: 375px; top: 27px; width: 400px; height: 60px;
    border-radius: 30px; background: var(--search-fill);
    border: 2px solid var(--search-edge);
    box-shadow: inset 0 2px 4px rgba(0,0,0,.5), 0 1px 0 rgba(255,255,255,.12);
  }
  .search-field svg { position: absolute; left: 20px; top: 18px; }

  .album-hero {
    position: absolute; left: 0; top: 116px; width: 800px; height: 312px;
    background: linear-gradient(var(--hero-top), var(--hero-bottom));
    box-shadow: 0 6px 10px rgba(60,50,90,.35);
  }
  .record-disc {
    position: absolute; left: 180px; top: 72px; width: 145px; height: 145px;
    border-radius: 50%; background: radial-gradient(circle, #555 0 7%, #111 8% 12%, #2b2b2b 13% 100%);
    box-shadow: 2px 3px 6px rgba(0,0,0,.4);
  }
  .album-cover {
    position: absolute; left: 105px; top: 64px; width: 182px; height: 182px;
    border-radius: 4px;
    background: radial-gradient(circle at 50% 55%, var(--cover-accent) 0 18%, var(--cover-paper) 40%, #d8c69f 100%);
    box-shadow: 3px 4px 8px rgba(0,0,0,.45);
  }
  .album-title {
    position: absolute; left: 410px; top: 82px;
    font-size: 30px; font-weight: 700; color: var(--text-light);
  }
  .album-meta { position: absolute; left: 412px; top: 128px; list-style: none; }
  .album-meta li { font-size: 22px; color: var(--text-soft); height: 34px; }
  .album-meta span { font-size: 18px; }

  .tracks-heading {
    position: absolute; left: 22px; top: 500px;
    font-size: 26px; font-weight: 700; display: flex; align-items: center; gap: 26px;
  }
  .track-list { position: absolute; left: 72px; top: 574px; width: 670px; list-style: none; }
  .track-list li {
    display: flex; justify-content: space-between;
    height: 43.75px; font-size: 19px; color: var(--text-soft);
  }

  .action {
    position: absolute; top: 858px; height: 89px; border-radius: 5px;
    border: 1px solid rgba(0,0,0,.55);
    display: flex; align-items: center; justify-content: center;
    font-size: 23px; font-weight: 700; color: var(--text-light);
    box-shadow: inset 0 1px 0 rgba(255,255,255,.25);
  }
  .action-add { left: 25px; width: 265px; background: linear-gradient(var(--green-top), var(--green-bottom)); }
  .action-cancel { left: 320px; width: 218px; background: linear-gradient(var(--red-top), var(--red-bottom)); }
  .action-wishlist { left: 557px; width: 218px; background: linear-gradient(var(--blue-top), var(--blue-bottom)); }

  .tab-bar {
    position: absolute; left: 0; top: 1055px; width: 800px; height: 145px;
    background: linear-gradient(var(--tab-top), var(--tab-bottom));
    border-top: 2px solid #4a4b4f;
    display: flex;
  }
  .tab { flex: 1; position: relative; }
  .tab svg { position: absolute; left: 50%; top: 18px; transform: translateX(-50%); }
  .tab-label {
    position: absolute; left: 0; right: 0; top: 98px; text-align: center;
    font-size: 26px; font-weight: 700; color: var(--tab-label);
  }
  .tab-active .tab-label { color: var(--text-light); }
</style>
</head>
<body>
  <header class="app-header">
    <div class="app-name">Spindle</div>
    <div class="search-field">
      <svg width="22" height="22" viewBox="0 0 22 22"><circle cx="9" cy="9" r="6.5" fill="none" stroke="#9a9ba0" stroke-width="2.5"/><line x1="14" y1="14" x2="20" y2="20" stroke="#9a9ba0" stroke-width="3" stroke-linecap="round"/></svg>
    </div>
  </header>

  <section class="album-hero">
    <div class="record-disc"></div>
    <div class="album-cover" role="img" aria-label="Album cover artwork"></div>
    <h1 class="album-title">NIGHT VOLT</h1>
    <ul class="album-meta">
      <li>Artist Name: <span>Couch Royal</span></li>
      <li>Release Year: <span>2005</span></li>
      <li>Labels: <span>Gritty Pressings</span></li>
    </ul>
  </section>

  <h2 class="tracks-heading">
    <svg width="22" height="36" viewBox="0 0 22 36"><ellipse cx="8" cy="29" rx="7.5" ry="6" fill="#fff"/><rect x="13" y="2" width="3" height="28" fill="#fff"/><path d="M16 2 C18 8 24 10 20 20 C21 13 18 11 16 10 Z" fill="#fff"/></svg>
    Tracks List
  </h2>
  <ul class="track-list">
    <li><span>Couch Royal</span><span>2:23</span></li>
    <li><span>Salt Market</span><span>3:23</span></li>
    <li><span>Back Lane</span><span>2:20</span></li>
    <li><span>KBTR</span><span>4:00</span></li>
    <li><span>Far From Us</span><span>2:43</span></li>
  </ul>

  <div class="action action-add">Add This Album</div>
  <div class="action action-cancel">Cancel</div>
  <div class="action action-wishlist">Wishlist</div>

  <nav class="tab-bar">
    <div class="tab">
      <svg width="84" height="60" viewBox="0 0 84 60" fill="var(--tab-icon)"><circle cx="22" cy="20" r="10"/><circle cx="62" cy="20" r="10"/><path d="M4 58 C4 38 40 38 40 58 Z"/><path d="M44 58 C44 38 80 38 80 58 Z"/><circle cx="42" cy="14" r="12"/><path d="M18 58 C18 30 66 30 66 58 Z"/></svg>
      <div class="tab-label">Artist</div>
    </div>
    <div class="tab tab-active">
      <svg width="72" height="72" viewBox="0 0 72 72"><circle cx="36" cy="36" r="35" fill="#fff"/><circle cx="36" cy="36" r="14" fill="#3a3b3e"/><circle cx="36" cy="36" r="6" fill="#fff"/></svg>
      <div class="tab-label">Albums</div>
    </div>
    <div class="tab">
      <svg width="66" height="64" viewBox="0 0 66 64" fill="var(--tab-icon)"><path d="M20 10 L62 2 L62 48 L56 48 L56 14 L26 20 L26 56 L20 56 Z"/><ellipse cx="13" cy="54" rx="12" ry="9"/><ellipse cx="52" cy="48" rx="12" ry="9"/></svg>
      <div class="tab-label">Song</div>
    </div>
    <div class="tab">
      <svg width="76" height="68" viewBox="0 0 76 68"><path d="M38 66 C10 44 2 32 2 20 C2 9 11 2 21 2 C29 2 35 7 38 13 C41 7 47 2 55 2 C65 2 74 9 74 20 C74 32 66 44 38 66 Z" fill="var(--tab-icon)"/></svg>
      <div class="tab-label">Wishlist</div>
    </div>
  </nav>
</body>
</html>
```